Multi-Line Insurance PPC Landing Page - Conversion optimized.

We have a PPC landing page used for the general population to get an insurance quote through an agent's site.

We'd like to improve the page for PPC traffic, make it more conversion friendly.

Site should be a single long page.

We will dynamically change the form and headlines on the page depending on what insurance "line" is being called. ie, Lift, Auto, Home, Business.

The enclosed AI file has all of the raw elements we need. We're looking to enhance the design and conversion ability.

Target Market(s)

General public needed insurance services.

Industry/Entity Type

Insurance Broker

Number of Pages Required

1 page

Font styles to use
Sans Serif

Requirements
Must have
• Form, agent picture, name, address.

```html
<!DOCTYPE html>
<html lang="en">
<head>
<meta charset="utf-8">
<title>Harbor Mutual – Insurance Quotes</title>
<link rel="stylesheet" href="https://fonts.googleapis.com/css2?family=Open+Sans:wght@400;600;700&display=swap">
<style>
:root{
  --red:#e0201b;
  --ink:#333;
  --muted:#888;
  --line:#e3e3e3;
  --field:#fff;
  --field-border:#cfcfcf;
  --btn:#3c3c3c;
  --footer:#2b2b2b;
  --footer-text:#9a9a9a;
  --page:#fff;
}
*{box-sizing:border-box;margin:0;padding:0}
html,body{width:730px;height:1200px;overflow:hidden;background:var(--page);font-family:"Open Sans",Arial,sans-serif;color:var(--ink)}
.page{position:relative;width:730px;height:1200px}

/* header */
.site-header{height:45px;display:flex;align-items:center;justify-content:space-between;padding:0 22px;background:#fff;border-bottom:1px solid var(--line)}
.brand{display:flex;align-items:center;gap:6px;color:var(--red);font-weight:700;font-size:17px}
.brand-dot{width:12px;height:12px;border-radius:50%;background:var(--red)}
.header-call{display:flex;flex-direction:column;align-items:flex-end;gap:2px}
.header-call small{font-size:8px;color:var(--muted)}
.phone-pill{background:var(--red);color:#fff;font-size:11px;font-weight:700;padding:2px 12px;border-radius:10px}

/* hero */
.hero{position:relative;height:275px;background:linear-gradient(160deg,#c7d8b4 0%,#8fae6a 45%,#5e7f3c 75%,#3f5a2a 100%)}
.hero-tag{position:absolute;right:48px;top:205px;color:#fff;font-size:17px;font-weight:600;line-height:1.2;text-shadow:0 1px 3px rgba(0,0,0,.35)}

/* coverage */
.coverage{padding:34px 60px 0;text-align:center}
.coverage-title{color:var(--red);font-size:17px;font-weight:700}
.coverage-intro{margin:10px auto 0;max-width:420px;font-size:8.5px;line-height:1.45;color:var(--muted)}
.lines{display:grid;grid-template-columns:repeat(3,1fr);column-gap:40px;row-gap:28px;margin-top:26px}
.line-card{display:flex;flex-direction:column;align-items:center}
.line-icon{width:32px;height:28px;fill:var(--red);stroke:var(--red)}
.line-name{margin-top:8px;color:var(--red);font-size:12px;font-weight:400}
.line-text{margin-top:6px;font-size:7.5px;line-height:1.45;color:var(--muted)}
.quote-btn{margin-top:10px;background:var(--btn);color:#fff;font-size:7.5px;font-weight:700;padding:5px 10px;border-radius:2px}

.rule{margin:28px 0 0;border:0;border-top:1px solid var(--line)}

/* quote form */
.quote{position:relative;padding:24px 0 0 65px}
.quote-title{color:var(--red);font-size:20px;font-weight:700;line-height:1.2}
.quote-sub{font-size:12px;color:var(--ink);margin-top:2px}
.quote-form{display:grid;grid-template-columns:140px 135px auto;column-gap:10px;row-gap:10px;margin-top:18px}
.field label{display:block;font-size:8px;color:var(--ink);margin-bottom:3px}
.input{height:22px;background:var(--field);border:1px solid var(--field-border);border-radius:2px;font-size:8px;color:var(--muted);padding:5px 6px;display:flex;justify-content:space-between;align-items:center}
.input.select::after{content:"▾";font-size:8px;color:var(--muted)}
.dob{display:flex;gap:4px}
.dob .input{flex:1}
.col-1{grid-column:1}
.col-2{grid-column:2}
.submit{grid-column:3;grid-row:4;align-self:end;justify-self:start;height:22px;display:flex;align-items:center;background:var(--btn);color:#fff;font-size:8.5px;padding:0 10px;border-radius:2px;white-space:nowrap}

.agent{position:absolute;left:428px;top:24px;width:170px;text-align:center}
.agent-name{color:var(--red);font-size:15px;font-weight:600;line-height:1.2}
.agent-address{font-size:8px;color:var(--muted);line-height:1.4;margin-top:2px}
.agent-phone{font-size:12px;font-weight:700;margin-top:2px}
.agent-photo{position:absolute;left:520px;top:98px;width:150px;height:265px;background:linear-gradient(180deg,#e9e4df 0%,#5a3b34 40%,#2d1c1a 100%);border-radius:60px 60px 0 0}

/* footer */
.site-footer{position:absolute;left:0;bottom:0;width:730px;height:105px;background:var(--footer);color:var(--footer-text);font-size:8px}
.footer-nav{display:flex;justify-content:center;gap:22px;padding-top:16px}
.footer-bottom{display:flex;justify-content:space-between;align-items:flex-start;padding:22px 22px 0;line-height:1.5}
.socials{display:flex;gap:5px;margin-top:4px}
.social{width:12px;height:12px;border-radius:50%;background:#4a4a4a}
.social.blue{background:#3a84c7}
.footer-agent{text-align:right}
</style>
</head>
<body>
<div class="page">
  <header class="site-header">
    <div class="brand"><span class="brand-dot"></span>Harbor Mutual</div>
    <div class="header-call"><small>Call for a quote today</small><span class="phone-pill">(555) 010-2468</span></div>
  </header>

  <section class="hero" role="img" aria-label="Family of three relaxing on the grass under a tree in a sunny park">
    <p class="hero-tag">Quisque aliquet<br>vestibulum pulvinar</p>
  </section>

  <section class="coverage">
    <h1 class="coverage-title">We cover all your insurance needs at the best prices, guaranteed</h1>
    <p class="coverage-intro">Following insurance coverage around your needs is easier than you think. We're here to help you learn more about all your options and provide answers to common questions. Ready to take the next step?</p>

    <div class="lines">
      <div class="line-card">
        <svg class="line-icon" viewBox="0 0 32 28"><path d="M5 13l3-7h16l3 7h2v9h-3v3h-4v-3H10v3H6v-3H3v-9z" stroke="none"/><rect x="9" y="8" width="14" height="5" fill="#fff" stroke="none"/><circle cx="8" cy="17" r="2" fill="#fff" stroke="none"/><circle cx="24" cy="17" r="2" fill="#fff" stroke="none"/></svg>
        <h2 class="line-name">Auto Insurance</h2>
        <p class="line-text">Protect every driver and vehicle with flexible plans, quick claims help and savings for safe drivers and bundled policies.</p>
        <span class="quote-btn">GET A QUOTE!</span>
      </div>
      <div class="line-card">
        <svg class="line-icon" viewBox="0 0 32 28"><path d="M16 2L2 14h4v12h8v-8h4v8h8V14h4z" stroke="none"/></svg>
        <h2 class="line-name">Home Insurance</h2>
        <p class="line-text">Cover your home, belongings and liability with options built around your property, your budget and the way you live.</p>
        <span class="quote-btn">GET A QUOTE!</span>
      </div>
      <div class="line-card">
        <svg class="line-icon" viewBox="0 0 32 28"><circle cx="16" cy="14" r="10" fill="none" stroke-width="5"/><circle cx="16" cy="14" r="10" fill="none" stroke="#fff" stroke-width="5" stroke-dasharray="7 8.7" stroke-dashoffset="3"/></svg>
        <h2 class="line-name">Life Insurance</h2>
        <p class="line-text">Give your family lasting security with term and permanent options, simple applications and friendly guidance at every step.</p>
        <span class="quote-btn">GET A QUOTE!</span>
      </div>
      <div class="line-card">
        <svg class="line-icon" viewBox="0 0 32 28" fill="none" stroke-width="2.5"><path d="M8 2v9a5 5 0 0 0 10 0V2"/><path d="M13 16v4a5 5 0 0 0 10 0v-5"/><circle cx="23" cy="12" r="3"/></svg>
        <h2 class="line-name">Health Insurance</h2>
        <p class="line-text">Find medical plans that fit your household, with trusted networks, clear pricing and support when choosing your coverage.</p>
        <span class="quote-btn">GET A QUOTE!</span>
      </div>
      <div class="line-card">
        <svg class="line-icon" viewBox="0 0 32 28"><path d="M11 6V3h10v3h8v19H3V6zm2 0h6V5h-6z" stroke="none"/><rect x="3" y="13" width="26" height="2" fill="#fff" stroke="none"/></svg>
        <h2 class="line-name">Business Insurance</h2>
        <p class="line-text">Keep your company running with property, liability and workers coverage shaped around your industry and daily operations.</p>
        <span class="quote-btn">GET A QUOTE!</span>
      </div>
      <div class="line-card">
        <svg class="line-icon" viewBox="0 0 32 28" fill="none" stroke-width="2.5"><circle cx="14" cy="3.5" r="2.5" fill="var(--red)" stroke="none"/><path d="M14 7v9h8l3 7"/><path d="M10 12a7 7 0 1 0 10 9"/></svg>
        <h2 class="line-name">Disability Insurance</h2>
        <p class="line-text">Replace part of your income if illness or injury stops you from working, so your bills stay paid on time.</p>
        <span class="quote-btn">GET A QUOTE!</span>
      </div>
    </div>
  </section>

  <hr class="rule">

  <section class="quote">
    <h2 class="quote-title">Get an instant life insurance quote.</h2>
    <p class="quote-sub">A fast are secure way to get a quote quickly.</p>

    <form class="quote-form">
      <div class="field col-1"><label>Full name</label><div class="input"></div></div>
      <div class="field col-2"><label>Height/Weight</label><div class="input"></div></div>
      <div class="field col-1"><label>Sex</label><div class="input select">Select</div></div>
      <div class="field col-2"><label>Tobacco Use</label><div class="input select">Select</div></div>
      <div class="field col-1"><label>Date of Birth</label><div class="dob"><div class="input select">Month</div><div class="input select">Day</div><div class="input select">Year</div></div></div>
      <div class="field col-2"><label>Mobile Phone</label><div class="input"></div></div>
      <div class="field col-1"><label>Coverage Amount</label><div class="input select">Select</div></div>
      <div class="field col-2"><label>Email</label><div class="input"></div></div>
      <span class="submit">Show me quotes!</span>
    </form>

    <div class="agent">
      <p class="agent-name">Owen Hartley - Agent</p>
      <p class="agent-address">482 Maple Avenue, Suite 210<br>Riverton, CA 90210</p>
      <p class="agent-phone">(555) 010-2468</p>
    </div>
    <div class="agent-photo" role="img" aria-label="Portrait of the insurance agent in a dark suit and red tie"></div>
  </section>

  <footer class="site-footer">
    <nav class="footer-nav">
      <span>Auto Insurance</span><span>Home Insurance</span><span>Life Insurance</span><span>Health Insurance</span><span>Business Insurance</span><span>Disability Insurance</span>
    </nav>
    <div class="footer-bottom">
      <div>
        <p>Copyright © 2015 Harbor Mutual. All rights reserved.</p>
        <p>Terms and Conditions | Privacy Policy | Sitemap</p>
      </div>
      <div class="socials"><span class="social"></span><span class="social blue"></span><span class="social"></span></div>
      <div class="footer-agent">
        <p>Owen Hartley - Agent | 482 Maple Avenue, Suite 210</p>
        <p>Riverton, CA 90210 | Phone (555) 010-2468</p>
      </div>
    </div>
  </footer>
</div>
</body>
</html>
```